Brightarc Orthodontics appointment card design

I need appointment cards/ business cards made. Front will be Logo, name, title, email, phone number and location (5263 Walnut Hollow Pkwy, Ste 412, Concord, NC 28027) . the back should have an appointment card (name, time, date) and also 3 addresses listed with a check box so we can check to which location they are going.
Dale Fenwick Orthodontics
- 6735 Orchard Street, Ste 514, Harrisburg, NC 28075
- 3647 Ridgeway Drive NE, Ste 810, Concord, NC 28025
- 2917 Thornbury Corporate Drive, Ste 605, Charlotte, NC 28277
Business card can be horizontal or vertical in Design.
I need to be able to edit it to update and add new employees

Requirements
Must have
• Front:
• - Logo
• - Name & Title (able to be edited)
• - phone (704-555-0186) & Email (need to be able to edit)
• - Address: 5263 Walnut Hollow Pkwy, Ste 412
• Concord, NC 28027
• Back:
• Appointment Card design:
• - Name, time, Date
• - 3 locations w/ a check box so the patient knows where to go:
• Dale Fenwick Orthodontics
• - 6735 Orchard Street, Ste 514, Harrisburg, NC 28075
• - 3647 Ridgeway Drive NE, Ste 810, Concord, NC 28025
• - 2917 Thornbury Corporate Drive, Ste 605, Charlotte, NC 28277

```html
<!DOCTYPE html>
<html lang="en">
<head>
<meta charset="utf-8">
<title>Brightarc Orthodontics – Appointment Card</title>
<link href="https://fonts.googleapis.com/css2?family=Lato:wght@400;700;900&family=Oswald:wght@600&display=swap" rel="stylesheet">
<style>
  :root {
    --brand-blue: #1b6dbd;
    --ink: #1f1f1f;
    --muted: #6d6e71;
    --paper: #ffffff;
    --backdrop: #2a2a2a;
  }
  * { box-sizing: border-box; margin: 0; padding: 0; }
  html, body { width: 1200px; height: 1200px; overflow: hidden; }
  body {
    background: var(--backdrop);
    font-family: "Lato", Arial, sans-serif;
    color: var(--ink);
    display: flex;
    flex-direction: column;
    align-items: center;
    justify-content: center;
    gap: 60px;
  }
  .card {
    position: relative;
    width: 900px;
    height: 514px;
    background: var(--paper);
  }
  .brand {
    position: absolute;
    display: flex;
    align-items: center;
    gap: 12px;
    font-family: "Lato", Arial, sans-serif;
    font-weight: 900;
    font-size: 40px;
    color: var(--brand-blue);
    letter-spacing: 0.5px;
    white-space: nowrap;
  }
  .brand__dot {
    width: 22px; height: 22px;
    border-radius: 50%;
    background: var(--brand-blue);
  }
  .rule {
    position: absolute;
    height: 2px;
    background: var(--brand-blue);
  }

  /* Front */
  .front .brand { left: 60px; top: 90px; }
  .front .address {
    position: absolute;
    right: 80px; top: 250px;
    text-align: right;
    font-size: 19px;
    line-height: 1.35;
    color: var(--ink);
  }
  .front .rule--long { left: 330px; right: 60px; top: 312px; }
  .front .person { position: absolute; left: 60px; top: 290px; }
  .person__name {
    font-family: "Oswald", "Arial Narrow", sans-serif;
    font-weight: 600;
    font-size: 34px;
    color: var(--brand-blue);
    letter-spacing: 0.5px;
    line-height: 1;
  }
  .person__title { font-size: 20px; margin-top: 6px; }
  .front .rule--short { left: 60px; width: 250px; top: 374px; }
  .contacts {
    position: absolute;
    left: 60px; top: 388px;
    list-style: none;
    font-size: 19px;
    line-height: 1.4;
  }
  .contacts li { display: flex; align-items: center; gap: 10px; }
  .contacts svg { width: 16px; height: 16px; fill: var(--brand-blue); flex: none; }

  /* Back */
  .back .brand { right: 60px; top: 60px; }
  .form { position: absolute; left: 60px; right: 60px; top: 190px; }
  .form__row { display: flex; align-items: flex-end; gap: 12px; margin-bottom: 26px; }
  .form__label { font-weight: 700; font-size: 22px; white-space: nowrap; }
  .form__line { flex: 1; height: 2px; background: var(--brand-blue); margin-bottom: 6px; }
  .locations { position: absolute; left: 60px; top: 310px; }
  .locations__practice { font-weight: 900; font-size: 24px; margin-bottom: 10px; }
  .locations__list { list-style: none; font-size: 23px; line-height: 1.5; }
  .locations__list li { display: flex; align-items: center; gap: 16px; }
  .checkbox {
    width: 20px; height: 20px;
    border: 2px solid var(--brand-blue);
    flex: none;
  }
  .checkbox--checked { background: var(--brand-blue); }
</style>
</head>
<body>

  <section class="card front" aria-label="Business card front">
    <div class="brand"><span class="brand__dot"></span>Brightarc Orthodontics</div>
    <p class="address">5263 Walnut Hollow Pkwy<br>Ste 412 - Concord, NC 28027</p>
    <div class="rule rule--long"></div>
    <div class="person">
      <p class="person__name">NORA WHITFIELD</p>
      <p class="person__title">CEO / Manager</p>
    </div>
    <div class="rule rule--short"></div>
    <ul class="contacts">
      <li><svg viewBox="0 0 16 16" aria-hidden="true"><path d="M3.6 1.5l2.3 2.6-1.4 1.8c.9 2 2.6 3.7 4.6 4.6l1.8-1.4 2.6 2.3-1.3 2.3C7.2 13.2 2.8 8.8 1.3 3z"/></svg>+704-555-0186</li>
      <li><svg viewBox="0 0 16 16" aria-hidden="true"><path d="M8 1a7 7 0 100 14A7 7 0 008 1zm0 1.5c.8 0 1.7 1.6 2 4H6c.3-2.4 1.2-4 2-4zM2.6 7.5h2c0-.9.2-3 1-4.3a5.5 5.5 0 00-3 4.3zm0 1h2c0 .9.2 3 1 4.3a5.5 5.5 0 01-3-4.3zM6 8.5h4c-.3 2.4-1.2 4-2 4s-1.7-1.6-2-4zm5.4 0h2a5.5 5.5 0 01-3 4.3c.8-1.3 1-3.4 1-4.3zm0-1c0-.9-.2-3-1-4.3a5.5 5.5 0 013 4.3z"/></svg>www.brightarcortho.com</li>
      <li><svg viewBox="0 0 16 16" aria-hidden="true"><path d="M1 3h14v10H1zm1.5 1.2v.3L8 8.6l5.5-4.1v-.3zm0 1.9v5.7h11V6.1L8 10.2z"/></svg>hello@brightarcortho.com</li>
    </ul>
  </section>

  <section class="card back" aria-label="Appointment card back">
    <div class="brand"><span class="brand__dot"></span>Brightarc Orthodontics</div>
    <div class="form">
      <div class="form__row">
        <span class="form__label">Name :</span><span class="form__line"></span>
        <span class="form__label">Date :</span><span class="form__line"></span>
      </div>
      <div class="form__row">
        <span class="form__label">Time :</span><span class="form__line"></span>
      </div>
    </div>
    <div class="locations">
      <p class="locations__practice">Dale Fenwick Orthodontics :</p>
      <ul class="locations__list">
        <li><span class="checkbox checkbox--checked"></span>6735 Orchard Street, Ste 514, Harrisburg, NC 28075</li>
        <li><span class="checkbox"></span>3647 Ridgeway Drive NE, Ste 810, Concord, NC 28025</li>
        <li><span class="checkbox"></span>2917 Thornbury Corporate Drive, Ste 605, Charlotte, NC 28277</li>
      </ul>
    </div>
  </section>

</body>
</html>
```